32 x 24 Swinging Real Estate Yard Sign

We are looking to design a new sign for our business to focus on the remodeling of homes to sell. We are looking to have a yard sign that gets peoples attention and is informational. The headline will be "The Secret to Top Dollar? Remodel First.". We remodel homes for sellers with no up front cost, as they simply pay at closing. This link has more info, https://bramblecresthomes.com/Remodel
The message we want to convey to those seeing the sign is we are a one stop shop, who can renovate your home and sell it for no stress. We are licensed real estate agents and licensed contractors.
Both of these license numbers and info need to be on the design:
CADRE #02794613
Contractors License #1178524
Email: info@bramblecresthomes.com
Phone: (408)614-2907
I'll attach a sample sign we have for our agents normally as well as all brand art work.
• Pantone Colors
o #172A41
Dark blue
o #4381B1
Medium blue
o #6FA6CC
Light blue
Target Market(s)
Residential Real Estate Sellers
Industry/Entity Type
Real Estate
Colors
Designer to choose colors to be used in the design.

```html
<!DOCTYPE html>
<html lang="en">
<head>
<meta charset="utf-8">
<title>Bramblecrest Homes – Remodel First Yard Sign</title>
<link href="https://fonts.googleapis.com/css2?family=League+Spartan:wght@600;700;800&family=Poppins:wght@300;600;700&display=swap" rel="stylesheet">
<style>
  :root {
    --dark-blue: #172A41;
    --medium-blue: #4381B1;
    --light-blue: #6FA6CC;
    --white: #ffffff;
    --backdrop: #f3f5f7;
  }
  html, body {
    margin: 0;
    padding: 0;
    width: 938px;
    height: 1200px;
    overflow: hidden;
    background: var(--backdrop);
  }
  .sign {
    position: absolute;
    left: 84px;
    top: 87px;
    width: 770px;
    height: 1025px;
    background: var(--white);
    overflow: hidden;
  }
  .sign-waves {
    position: absolute;
    inset: 0;
    width: 770px;
    height: 1025px;
  }
  .brand {
    position: absolute;
    top: 88px;
    left: 0;
    width: 100%;
    display: flex;
    justify-content: center;
    align-items: center;
    gap: 14px;
  }
  .brand-dot {
    width: 26px;
    height: 26px;
    border-radius: 50%;
    background: var(--medium-blue);
  }
  .brand-name {
    font-family: "League Spartan", sans-serif;
    font-weight: 600;
    font-size: 40px;
    letter-spacing: 1px;
    color: var(--dark-blue);
    line-height: 1;
  }
  .line {
    position: absolute;
    left: 0;
    width: 100%;
    margin: 0;
    text-align: center;
    line-height: 1;
    white-space: nowrap;
  }
  .headline {
    font-family: "League Spartan", sans-serif;
    font-weight: 800;
    color: var(--dark-blue);
    font-size: 61px;
  }
  .headline-1 { top: 192px; }
  .headline-2 { top: 252px; }
  .callout {
    font-family: "League Spartan", sans-serif;
    font-weight: 800;
    color: var(--medium-blue);
    font-size: 110px;
    letter-spacing: -1px;
  }
  .callout-1 { top: 316px; }
  .callout-2 { top: 419px; }
  .license {
    font-family: "League Spartan", sans-serif;
    font-weight: 700;
    color: var(--dark-blue);
    font-size: 34px;
  }
  .license .number { color: var(--medium-blue); }
  .license-1 { top: 521px; }
  .license-2 { top: 567px; }
  .phone {
    top: 728px;
    font-family: "Poppins", sans-serif;
    font-weight: 700;
    font-size: 80px;
    letter-spacing: -2px;
    color: var(--white);
  }
  .email {
    top: 818px;
    font-family: "Poppins", sans-serif;
    font-weight: 600;
    font-size: 40px;
    color: var(--white);
  }
  .website {
    top: 926px;
    font-family: "Poppins", sans-serif;
    font-weight: 300;
    font-size: 42px;
    color: var(--white);
  }
  .website .domain {
    font-weight: 600;
    color: var(--dark-blue);
  }
</style>
</head>
<body>
  <main class="sign">
    <svg class="sign-waves" viewBox="0 0 770 1025" aria-hidden="true">
      <rect x="0" y="897" width="770" height="128" fill="var(--light-blue)"/>
      <path d="M0,594 C200,690 360,705 470,672 C550,640 600,600 690,610 C730,616 755,630 770,642 L770,897 L0,897 Z" fill="var(--medium-blue)"/>
      <path d="M0,650 C160,705 340,735 480,690 C550,666 600,630 665,628 C715,628 745,662 770,688 L770,900 L0,900 Z" fill="var(--dark-blue)" stroke="var(--white)" stroke-width="9"/>
    </svg>

    <div class="brand">
      <span class="brand-dot"></span>
      <span class="brand-name">BRAMBLECREST HOMES</span>
    </div>

    <h1 class="line headline headline-1">THE SECRET TO</h1>
    <p class="line headline headline-2">TOP DOLLAR?</p>
    <p class="line callout callout-1">REMODEL</p>
    <p class="line callout callout-2">FIRST</p>

    <p class="line license license-1">CONTRACTORS LICENSE <span class="number">#1178524</span></p>
    <p class="line license license-2">CADRE <span class="number">#02794613</span></p>

    <p class="line phone">(408)614-2907</p>
    <p class="line email">info@bramblecresthomes.com</p>
    <p class="line website">www.<span class="domain">bramblecresthomes</span>.com</p>
  </main>
</body>
</html>
```